Networking Events Calendar/Diary

We need a responsive website that can act as both an online diary/calendar and a resource for community and networking events similar to brimtolvenquarrix.com (we do not want a clone, but one with similar functionality). We need to be able to host adverts, have a client area for clients to add their own events to the diary. This needs to have the functionality that clients have to pay to add recurring events. Some integration would be useful so that if a clients already has their own online diary on their website then using an API possibly to also add that event into our online diary

Industry/Entity Type

Events

Coding

Coded - Design and coding required

Number of Pages Required

5+ page

Requirements
Must have
• My project must have a calendar area, space for ads, be responsive and easily viewable on mobile. A subscribers area for clients and a way to purchase premium status so that premium events are highlighted.

```html
<!DOCTYPE html>
<html lang="en">
<head>
<meta charset="utf-8">
<title>Orvo Events</title>
<link rel="stylesheet" href="https://fonts.googleapis.com/css2?family=Open+Sans:wght@400;600;700;800&display=swap">
<style>
:root{
  --blue:#1aa6e0;
  --ink:#333333;
  --text:#6a6a6a;
  --muted:#9a9a9a;
  --rule:#dddddd;
  --panel:#f1f1f1;
  --nav-active:#4a4a4a;
  --tab-dark:#4d4d4d;
  --footer:#272727;
  --footer-text:#8a8a8a;
  --white:#ffffff;
}
*{box-sizing:border-box;margin:0;padding:0}
html,body{width:1200px;height:2270px;overflow:hidden}
body{position:relative;background:var(--white);font-family:"Open Sans",Arial,sans-serif;color:var(--text)}
.abs{position:absolute}
.logo{font-weight:800;font-size:27px;letter-spacing:3px;color:#444;text-transform:uppercase;white-space:nowrap}
.ad{border:1px solid #ccc}
.nav{left:0;top:118px;width:1200px;height:45px;background:linear-gradient(#16b3f0,#0a9ad8)}
.nav-item{top:0;height:45px;line-height:45px;font-size:12px;font-weight:600;color:var(--white);text-transform:uppercase;white-space:nowrap}
.nav-item.active{background:var(--nav-active);padding:0 21px}
.hero{left:162px;top:177px;width:876px;height:446px;border-top:4px solid var(--blue);background:linear-gradient(100deg,#6d6f74 0%,#9aa3ad 35%,#3c3f44 70%,#24262a 100%)}
.hero-title{left:36px;top:304px;font-size:22px;font-weight:700;color:var(--white);text-transform:uppercase}
.hero-text{left:33px;top:352px;width:380px;font-size:15px;line-height:23px;color:var(--white)}
.dot{top:404px;width:8px;height:8px;border-radius:50%;background:var(--white)}
.dot.on{background:var(--blue)}
.section-title{font-size:18px;font-weight:700;color:var(--ink);text-transform:uppercase}
.section-title span{color:var(--blue)}
.section-rule{height:1px;background:var(--rule);width:610px}
.section-rule::before{content:"";position:absolute;left:0;top:-1px;width:46px;height:3px;background:var(--blue)}
.card-title{font-size:15px;font-weight:700;color:var(--ink);line-height:23px}
.card-text{font-size:11px;line-height:19px;color:var(--text)}
.meta{font-size:11px;color:var(--blue);white-space:nowrap}
.meta svg{vertical-align:-1px;margin:0 2px}
.tab{top:657px;height:33px;line-height:33px;font-size:11px;font-weight:700;color:var(--white);text-transform:uppercase;text-align:center}
.side-list{left:812px;top:690px;width:226px;height:333px;background:var(--panel)}
.side-item{left:0;width:226px;height:83px;border-bottom:1px solid #ddd}
.side-item .thumb{left:21px;top:17px;width:62px;height:50px}
.side-item .txt{left:93px;top:14px;font-size:11px;line-height:16px;color:var(--text);white-space:nowrap}
.side-item .date{left:93px;top:52px;font-size:10px;color:var(--text)}
.cal-head{left:812px;top:1250px;width:226px;height:33px;line-height:33px;padding-left:15px;background:var(--blue);font-size:11px;font-weight:700;color:var(--white);text-transform:uppercase}
.cal-box{left:812px;top:1283px;width:226px;height:169px;border:1px solid #e5e5e5;border-top:0;overflow:hidden}
.cal-faint{left:80px;top:36px;font-size:34px;font-weight:700;color:#ececec;line-height:44px;white-space:nowrap}
.cal-row{left:15px;width:185px;font-size:12px;color:var(--ink);display:flex;justify-content:space-between}
.tw-box{left:812px;top:1473px;width:226px;height:272px;border:1px solid #e8e8e8}
.tw-title{left:12px;top:12px;font-size:15px;font-weight:700;color:var(--ink)}
.tw-follow{left:154px;top:14px;width:47px;height:17px;border:1px solid #ccc;border-radius:3px;background:#f4f4f4;font-size:9px;line-height:15px;text-align:center;color:#333}
.tw-item .thumb{left:12px;width:60px;height:50px}
.tw-item .txt{left:82px;font-size:10px;line-height:15px;color:var(--ink);white-space:nowrap}
.tw-item .txt b{font-weight:400;font-style:italic;color:var(--blue)}
.tw-item .by{left:82px;font-size:9px;color:var(--muted)}
.footer{left:0;top:2024px;width:1200px;height:246px;background:var(--footer)}
.f-logo{left:162px;top:30px;font-size:20px;font-weight:800;letter-spacing:2px;color:#bbb;text-transform:uppercase;white-space:nowrap}
.f-text{font-size:10px;line-height:18px;color:var(--footer-text)}
.f-title{font-size:14px;color:#ddd;text-transform:uppercase}
.f-line{font-size:11px;color:#aaa}
.f-input{left:673px;top:105px;width:161px;height:34px;background:#1b1b1b;font-size:10px;line-height:34px;padding-left:12px;color:#666}
.f-btn{left:834px;top:105px;width:69px;height:34px;background:var(--blue);color:var(--white);font-size:12px;font-weight:700;line-height:34px;text-align:center;text-transform:uppercase}
.f-social{left:958px;font-size:11px;color:#bbb}
.f-social i{display:inline-block;width:7px;height:7px;background:#999;margin-right:11px}
.f-bottom{left:0;top:207px;width:1200px;text-align:center;font-size:11px;color:#ddd;word-spacing:2px}
.f-bottom span{margin:0 6px}
</style>
</head>
<body>

<header>
  <div class="abs logo" style="left:162px;top:46px">Orvo Events</div>
  <div class="abs ad" role="img" aria-label="Advertisement banner for a Veltrona home entertainment player with Streamly app" style="left:583px;top:38px;width:455px;height:56px;background:linear-gradient(90deg,#e9eef5,#ffffff 45%,#d9dde4 80%,#c8282c 100%)"></div>
</header>

<nav class="abs nav">
  <div class="abs nav-item active" style="left:162px">Home</div>
  <div class="abs nav-item" style="left:256px">Events by Region</div>
  <div class="abs nav-item" style="left:396px">Events for Women</div>
  <div class="abs nav-item" style="left:548px">Workshops</div>
  <div class="abs nav-item" style="left:657px">Business Shows</div>
  <div class="abs nav-item" style="left:791px">Blog News</div>
  <div class="abs nav-item" style="left:903px">Contact Us</div>
  <svg class="abs" style="left:1012px;top:16px" width="14" height="14" viewBox="0 0 14 14"><circle cx="5" cy="5" r="3.6" fill="none" stroke="#fff" stroke-width="1.8"/><line x1="7.8" y1="7.8" x2="12.5" y2="12.5" stroke="#fff" stroke-width="2.2"/></svg>
</nav>

<section class="abs hero" role="img" aria-label="Photo of business people talking and smiling around a meeting table">
  <h1 class="abs hero-title">Welcome to Orvo Events</h1>
  <p class="abs hero-text">Maecenas mauris elementum, est morbi interdum curslorem us at elite imperdiet libero. Proin odios nteger an nulla augue pharetra cursus.</p>
  <span class="abs dot" style="left:800px"></span>
  <span class="abs dot on" style="left:812px"></span>
  <span class="abs dot" style="left:824px"></span>
  <span class="abs dot" style="left:836px"></span>
</section>

<h2 class="abs section-title" style="left:162px;top:646px">Latest <span>Events</span></h2>
<div class="abs section-rule" style="left:162px;top:678px"></div>

<article>
  <div class="abs" role="img" aria-label="Overhead photo of a team working with laptops at a wooden table" style="left:162px;top:703px;width:187px;height:143px;background:linear-gradient(135deg,#b8946a,#7d6a5a 60%,#4d5668)"></div>
  <h3 class="abs card-title" style="left:162px;top:856px;width:200px">Lorem ipsum dolor smet sed do eiusmod.</h3>
  <p class="abs card-text" style="left:162px;top:908px;width:195px">Sed ut perspiciatis unde omnis ist enatus error sit voluptatem loreacc usan tium doloremque laudant</p>
  <div class="abs meta" style="left:162px;top:979px">John Doe - <svg width="9" height="9" viewBox="0 0 9 9"><rect x=".5" y="1.5" width="8" height="7" fill="none" stroke="#1aa6e0"/><rect x=".5" y="1.5" width="8" height="2" fill="#1aa6e0"/></svg>Dec 12, 2015</div>
</article>
<article>
  <div class="abs" role="img" aria-label="Photo of a crowd of people networking in a bright hall" style="left:374px;top:703px;width:187px;height:143px;background:linear-gradient(135deg,#e8ecef,#b9c3cc 55%,#6f7f93)"></div>
  <h3 class="abs card-title" style="left:374px;top:856px;width:200px">Lorem ipsum dolor smet sed do eiusmod.</h3>
  <p class="abs card-text" style="left:374px;top:908px;width:195px">Sed ut perspiciatis unde omnis ist enatus error sit voluptatem loreacc usan tium doloremque laudant</p>
  <div class="abs meta" style="left:374px;top:979px">John Doe - <svg width="9" height="9" viewBox="0 0 9 9"><rect x=".5" y="1.5" width="8" height="7" fill="none" stroke="#1aa6e0"/><rect x=".5" y="1.5" width="8" height="2" fill="#1aa6e0"/></svg>Dec 12, 2015</div>
</article>
<article>
  <div class="abs" role="img" aria-label="Photo of a woman working on a laptop" style="left:586px;top:703px;width:187px;height:143px;background:linear-gradient(135deg,#eef0f2,#c9ced4 50%,#5b6472)"></div>
  <h3 class="abs card-title" style="left:586px;top:856px;width:200px">Lorem ipsum dolor smet sed do eiusmod.</h3>
  <p class="abs card-text" style="left:586px;top:908px;width:195px">Sed ut perspiciatis unde omnis ist enatus error sit voluptatem loreacc usan tium doloremque laudant</p>
  <div class="abs meta" style="left:586px;top:979px">John Doe - <svg width="9" height="9" viewBox="0 0 9 9"><rect x=".5" y="1.5" width="8" height="7" fill="none" stroke="#1aa6e0"/><rect x=".5" y="1.5" width="8" height="2" fill="#1aa6e0"/></svg>Dec 12, 2015</div>
</article>

<div class="abs tab" style="left:812px;width:74px;background:var(--blue)">Popular</div>
<div class="abs tab" style="left:886px;width:70px;background:var(--tab-dark)">Recent</div>
<div class="abs tab" style="left:956px;width:82px;background:var(--tab-dark)">Comments</div>
<div class="abs side-list">
  <div class="abs side-item" style="top:0">
    <div class="abs thumb" role="img" aria-label="Photo of a business meeting" style="background:linear-gradient(135deg,#d6d9de,#7d8797)"></div>
    <p class="abs txt">Sue ipsa quae ab illoive<br>ntore lorem veritatis</p>
    <p class="abs date">&#9633; Oct 08 2015</p>
  </div>
  <div class="abs side-item" style="top:83px">
    <div class="abs thumb" role="img" aria-label="Photo of a glowing digital network" style="background:linear-gradient(135deg,#0f2a4a,#2f7bb8)"></div>
    <p class="abs txt">Sue ipsa quae ab illoive<br>ntore lorem veritatis</p>
    <p class="abs date">&#9633; Oct 08 2015</p>
  </div>
  <div class="abs side-item" style="top:166px">
    <div class="abs thumb" role="img" aria-label="Photo of colleagues discussing at a desk" style="background:linear-gradient(135deg,#e2d6c8,#9b7d66)"></div>
    <p class="abs txt">Sue ipsa quae ab illoive<br>ntore lorem veritatis</p>
    <p class="abs date">&#9633; Oct 08 2015</p>
  </div>
  <div class="abs side-item" style="top:249px;border-bottom:0">
    <div class="abs thumb" role="img" aria-label="Photo of network cables" style="background:linear-gradient(135deg,#1f3f66,#5b9ad0)"></div>
    <p class="abs txt">Sue ipsa quae ab illoive<br>ntore lorem veritatis</p>
    <p class="abs date">&#9633; Oct 08 2015</p>
  </div>
</div>

<h2 class="abs section-title" style="left:162px;top:1043px">Latest <span>Blog Posts</span></h2>
<div class="abs section-rule" style="left:162px;top:1074px"></div>

<article>
  <div class="abs" role="img" aria-label="Photo of smiling business team standing together" style="left:162px;top:1100px;width:194px;height:142px;background:linear-gradient(135deg,#2e3440,#8a95a5 55%,#c9ced6)"></div>
  <div class="abs meta" style="left:381px;top:1101px">Business / by John Doe - <svg width="9" height="9" viewBox="0 0 9 9"><rect x=".5" y="1.5" width="8" height="7" fill="none" stroke="#1aa6e0"/><rect x=".5" y="1.5" width="8" height="2" fill="#1aa6e0"/></svg>Dec 12, 2015</div>
  <h3 class="abs card-title" style="left:379px;top:1123px;width:400px">Lorem ipsum dolor sit amet, consectetur adipiscinelit sed do eiusmod tempor incididunt ut labo.</h3>
  <p class="abs card-text" style="left:379px;top:1181px;width:395px">Sed ut perspiciatis unde omnis iste natus error sit voluptatem accusantium doloremque laudantium, totam rem aperiam, eaque ipsa quae ab illo inve ntore veritatis et quasi architecto beatae vitae dicta sunt explic.</p>
</article>
<article>
  <div class="abs" role="img" aria-label="Photo of hands holding a tablet with floating profile images" style="left:162px;top:1275px;width:194px;height:142px;background:linear-gradient(135deg,#5b6670,#a4adb6 55%,#3a4450)"></div>
  <div class="abs meta" style="left:381px;top:1277px">Business / by John Doe - <svg width="9" height="9" viewBox="0 0 9 9"><rect x=".5" y="1.5" width="8" height="7" fill="none" stroke="#1aa6e0"/><rect x=".5" y="1.5" width="8" height="2" fill="#1aa6e0"/></svg>Dec 12, 2015</div>
  <h3 class="abs card-title" style="left:379px;top:1299px;width:400px">Lorem ipsum dolor sit amet, consectetur adipiscinelit sed do eiusmod tempor incididunt ut labo.</h3>
  <p class="abs card-text" style="left:379px;top:1357px;width:395px">Sed ut perspiciatis unde omnis iste natus error sit voluptatem accusantium doloremque laudantium, totam rem aperiam, eaque ipsa quae ab illo inve ntore veritatis et quasi architecto beatae vitae dicta sunt explic.</p>
</article>

<div class="abs ad" role="img" aria-label="Advertisement supporting squash for the Summer Games with a click me button" style="left:812px;top:1042px;width:226px;height:188px;border-color:#e3e3e3;background:linear-gradient(160deg,#eaf4fb,#ffffff 40%,#fff4e0 100%)"></div>

<div class="abs cal-head">Calendar Events</div>
<div class="abs cal-box">
  <div class="abs cal-faint">DEC<br>12, 2015</div>
  <div class="abs cal-row" style="top:17px"><span>Commodities</span><span>( 4 )</span></div>
  <div class="abs cal-row" style="top:40px"><span>Currencies</span><span>( 5 )</span></div>
  <div class="abs cal-row" style="top:63px"><span>Economics</span><span>( 30 )</span></div>
  <div class="abs cal-row" style="top:86px"><span>International</span><span>( 41 )</span></div>
  <div class="abs cal-row" style="top:109px"><span>Politics</span><span>( 7 )</span></div>
  <div class="abs cal-row" style="top:132px"><span>Stocks</span><span>( 5 )</span></div>
</div>

<aside class="abs tw-box">
  <div class="abs tw-title">Posts</div>
  <div class="abs tw-follow">Follow</div>
  <div class="tw-item">
    <div class="abs thumb" role="img" aria-label="Photo of a person skiing" style="top:57px;background:linear-gradient(135deg,#cfe3f1,#4d84b3)"></div>
    <p class="abs txt" style="top:57px">Cum sociis <b>@pelvarine</b><br>magnis dis partu.</p>
    <p class="abs by" style="top:90px">Retweeted by Andrew</p>
  </div>
  <div class="tw-item">
    <div class="abs thumb" role="img" aria-label="Photo of hands using a tablet" style="top:128px;background:linear-gradient(135deg,#4e6b89,#a7bfd4)"></div>
    <p class="abs txt" style="top:128px">Cum sociis <b>@pelvarine</b><br>magnis dis partu.</p>
    <p class="abs by" style="top:161px">Retweeted by Andrew</p>
  </div>
  <div class="tw-item">
    <div class="abs thumb" role="img" aria-label="Photo of an underwater scene" style="top:199px;background:linear-gradient(135deg,#0e5b86,#3ab0d9)"></div>
    <p class="abs txt" style="top:199px">Cum sociis <b>@pelvarine</b><br>magnis dis partu.</p>
    <p class="abs by" style="top:232px">Retweeted by Andrew</p>
  </div>
</aside>

<h2 class="abs section-title" style="left:162px;top:1461px">Networking <span>News</span></h2>
<div class="abs section-rule" style="left:162px;top:1494px"></div>

<article>
  <div class="abs" role="img" aria-label="Illustration of the globe wrapped in glowing network lines" style="left:162px;top:1519px;width:300px;height:168px;background:radial-gradient(circle at 45% 70%,#2e7fc0,#0b2a4d 55%,#050d1a)"></div>
  <h3 class="abs card-title" style="left:162px;top:1702px;width:320px">Lorem ipsum dolor smetsed do eiusmod.</h3>
  <p class="abs card-text" style="left:162px;top:1736px;width:305px">Sed ut perspiciatis unde omnis istenatus error sit voluptla-tem loreaccusan tium doloremque laudantquasi architecto beatae vitae dicta sunt explic.</p>
  <div class="abs meta" style="left:162px;top:1804px">John Doe - <svg width="9" height="9" viewBox="0 0 9 9"><rect x=".5" y="1.5" width="8" height="7" fill="none" stroke="#1aa6e0"/><rect x=".5" y="1.5" width="8" height="2" fill="#1aa6e0"/></svg>Dec 12, 2015</div>
</article>
<article>
  <div class="abs" role="img" aria-label="Photo of business people silhouetted against a bright window" style="left:492px;top:1519px;width:113px;height:86px;background:linear-gradient(180deg,#d9dde2,#6f7780 60%,#2b2f35)"></div>
  <p class="abs card-text" style="left:623px;top:1519px;width:150px">Sed ut perspiciatilores unde omnis istenatus erroirt aspe rnatur aut odit aut fugit</p>
  <div class="abs meta" style="left:623px;top:1589px">John Doe - <svg width="9" height="9" viewBox="0 0 9 9"><rect x=".5" y="1.5" width="8" height="7" fill="none" stroke="#1aa6e0"/><rect x=".5" y="1.5" width="8" height="2" fill="#1aa6e0"/></svg>Dec 12, 2015</div>
</article>
<article>
  <div class="abs" role="img" aria-label="Photo of colleagues chatting at an event" style="left:492px;top:1623px;width:113px;height:87px;background:linear-gradient(135deg,#eef0f2,#a9b1bd 55%,#6a7382)"></div>
  <p class="abs card-text" style="left:623px;top:1623px;width:150px">Sed ut perspiciatilores unde omnis istenatus erroirt aspe rnatur aut odit aut fugit</p>
  <div class="abs meta" style="left:623px;top:1693px">John Doe - <svg width="9" height="9" viewBox="0 0 9 9"><rect x=".5" y="1.5" width="8" height="7" fill="none" stroke="#1aa6e0"/><rect x=".5" y="1.5" width="8" height="2" fill="#1aa6e0"/></svg>Dec 12, 2015</div>
</article>
<article>
  <div class="abs" role="img" aria-label="Photo of a server room with blue lights" style="left:492px;top:1729px;width:113px;height:87px;background:linear-gradient(135deg,#0c1f3a,#2a5d95 60%,#0c1f3a)"></div>
  <p class="abs card-text" style="left:623px;top:1729px;width:150px">Sed ut perspiciatilores unde omnis istenatus erroirt aspe rnatur aut odit aut fugit</p>
  <div class="abs meta" style="left:623px;top:1799px">John Doe - <svg width="9" height="9" viewBox="0 0 9 9"><rect x=".5" y="1.5" width="8" height="7" fill="none" stroke="#1aa6e0"/><rect x=".5" y="1.5" width="8" height="2" fill="#1aa6e0"/></svg>Dec 12, 2015</div>
</article>

<div class="abs ad" role="img" aria-label="Advertisement for Lumen Arc Partners at the convergence of art and technology" style="left:222px;top:1905px;width:749px;height:74px;border:0;background:linear-gradient(90deg,#0a0a0a 0%,#1a1a1a 35%,#c2461c 50%,#2a1a30 62%,#0a0a0a 100%)"></div>

<footer class="abs footer">
  <div class="abs f-logo">Orvo Events</div>
  <p class="abs f-text" style="left:162px;top:78px;width:240px">Excepteur sint occaecat cupidatat non proident, sunt inExcepteur sint occaecat cupidatat non proident, sunt in culpa qui officia deserunt mollit anim culpa.</p>

  <div class="abs f-title" style="left:415px;top:27px">Contact Us</div>
  <p class="abs f-line" style="left:415px;top:57px;width:210px;line-height:18px">14 Harrowmere Road Calloway Lane London N4 2QT</p>
  <svg class="abs" style="left:417px;top:103px" width="14" height="14" viewBox="0 0 14 14"><path d="M3 1l2.5 3-1.5 1.5c.8 1.8 2.2 3.2 4 4L9.5 8l3 2.5-1.5 2c-5 0-10-5-10-10z" fill="none" stroke="#aaa" stroke-width="1.2"/></svg>
  <p class="abs f-line" style="left:447px;top:103px">+44 20 5550 1842</p>
  <svg class="abs" style="left:417px;top:127px" width="14" height="11" viewBox="0 0 14 11"><rect x=".6" y=".6" width="12.8" height="9.8" fill="none" stroke="#aaa" stroke-width="1.2"/><path d="M.6 .6L7 6l6.4-5.4" fill="none" stroke="#aaa" stroke-width="1.2"/></svg>
  <p class="abs f-line" style="left:447px;top:125px">info@mailcorner.com</p>

  <div class="abs f-title" style="left:673px;top:27px">Newsletter</div>
  <p class="abs f-text" style="left:673px;top:56px;width:235px">Excepteur sint occaecat cupidatat non proident, sunt in culpa qui officia deserunt mollit anim</p>
  <div class="abs f-input">Enter your email address</div>
  <div class="abs f-btn">Sign Up</div>

  <div class="abs f-title" style="left:958px;top:25px">Social</div>
  <div class="abs f-social" style="top:53px"><i></i>Friendwall</div>
  <div class="abs f-social" style="top:77px"><i></i>Chirper</div>
  <div class="abs f-social" style="top:101px"><i></i>Circlepage</div>
  <div class="abs f-social" style="top:125px"><i></i>Clipstream</div>

  <div class="abs f-bottom"><span>Home</span><span>About</span><span>Advertise With Us</span><span>Privacy Policy</span><span>Terms of Service</span><span>&copy; 2015 Orvo Events. All Rights Reserved</span></div>
</footer>

</body>
</html>
```